TALMORK

The business want a professional looking business card. We have a scetch we will add but want the extra upgrade, and would like more suggestions for variations of our business cards.

```html
<!DOCTYPE html>
<html lang="en">
<head>
<meta charset="utf-8">
<title>TALMORK Business Card</title>
<link rel="stylesheet" href="https://fonts.googleapis.com/css2?family=Cinzel:wght@400&family=Montserrat:wght@400;700&display=swap">
<style>
  :root {
    --canvas-bg: #161616;
    --card-dark: #0d0d0d;
    --gold: #c9a548;
    --gold-deep: #a9852f;
    --gold-light: #e2c676;
    --white: #f2f2f2;
    --front-embossed: #b08a33;
  }
  * { margin: 0; padding: 0; box-sizing: border-box; }
  html, body { width: 900px; height: 1200px; overflow: hidden; }
  body { background: var(--canvas-bg); position: relative; font-family: "Montserrat", sans-serif; }

  .card {
    position: absolute;
    left: 136px;
    width: 630px;
    height: 357px;
    border-radius: 10px;
    overflow: hidden;
  }

  /* Front */
  .card-front { top: 215px; }
  .front-pattern {
    position: absolute; inset: 0;
    background: linear-gradient(90deg, #ece5d6 0%, #ddc98f 30%, #c8a552 60%, #a57c34 85%, #8b6227 100%);
  }
  .front-brand {
    position: absolute; left: 0; right: 0; top: 128px;
    text-align: center;
    font-family: "Cinzel", serif;
    font-size: 60px;
    letter-spacing: 14px;
    padding-left: 14px;
    color: var(--front-embossed);
    line-height: 1;
  }
  .front-since {
    position: absolute; left: 0; right: 0; top: 210px;
    text-align: center;
    font-family: "Montserrat", sans-serif;
    font-size: 19px;
    letter-spacing: 11px;
    padding-left: 11px;
    color: #8a6a2e;
  }

  /* Back */
  .card-back { top: 630px; background: var(--card-dark); }
  .back-info { position: absolute; left: 50px; top: 58px; }
  .holder-heading {
    font-family: "Cinzel", serif;
    font-size: 30px;
    color: var(--gold);
    line-height: 1;
    letter-spacing: 0.5px;
  }
  .holder-role {
    margin-top: 14px;
    font-size: 22px;
    color: var(--white);
    letter-spacing: 1px;
  }
  .holder-name {
    margin-top: 10px;
    font-size: 21px;
    font-weight: 700;
    color: var(--gold);
    letter-spacing: 1px;
  }
  .contact-list { list-style: none; margin-top: 46px; }
  .contact-list li {
    display: flex; align-items: center; gap: 6px;
    font-size: 18.5px;
    color: var(--white);
    letter-spacing: 1.5px;
    height: 29.5px;
  }
  .contact-list svg { width: 12px; height: 12px; flex: none; margin-top: 4px; }

  .back-brand {
    position: absolute; left: 370px; width: 260px; top: 108px;
    text-align: center;
  }
  .brand-square {
    width: 54px; height: 54px;
    margin: 0 auto 32px;
    background: var(--gold);
    transform: rotate(45deg);
  }
  .brand-name {
    font-family: "Cinzel", serif;
    font-size: 30px;
    letter-spacing: 9px;
    padding-left: 9px;
    color: var(--gold);
    line-height: 1;
  }
  .brand-since {
    margin-top: 8px;
    font-size: 10px;
    letter-spacing: 6px;
    padding-left: 6px;
    color: var(--gold);
  }
</style>
</head>
<body>

  <section class="card card-front">
    <div class="front-pattern" role="img" aria-label="Gold foil background with repeating floral lattice pattern"></div>
    <div class="front-brand">TALMORK</div>
    <div class="front-since">SINCE 2026</div>
  </section>

  <section class="card card-back">
    <div class="back-info">
      <h1 class="holder-heading">TALMORK HAUGLAND</h1>
      <p class="holder-role">CEO &amp; Founder</p>
      <p class="holder-name">Arne Solvik Haugland</p>
      <ul class="contact-list">
        <li>
          <svg viewBox="0 0 12 12" aria-hidden="true"><rect x="3" y="0.5" width="6" height="11" rx="1" fill="none" stroke="#c9a548" stroke-width="1.2"/><rect x="5" y="9.2" width="2" height="1" fill="#c9a548"/></svg>
          004791572046
        </li>
        <li>
          <svg viewBox="0 0 12 12" aria-hidden="true"><rect x="0.5" y="2.5" width="11" height="7.5" fill="#c9a548"/><path d="M0.5 2.5 L6 7 L11.5 2.5" fill="none" stroke="#0d0d0d" stroke-width="1"/></svg>
          talmork.llc@postkasse.no
        </li>
        <li>
          <svg viewBox="0 0 12 12" aria-hidden="true"><g fill="none" stroke="#c9a548" stroke-width="1"><circle cx="6" cy="6" r="5"/><ellipse cx="6" cy="6" rx="2.2" ry="5"/><path d="M1 6 H11 M2 3.3 H10 M2 8.7 H10"/></g></svg>
          www.talmork.llc
        </li>
      </ul>
    </div>

    <div class="back-brand">
      <div class="brand-square"></div>
      <div class="brand-name">TALMORK</div>
      <div class="brand-since">SINCE 2026</div>
    </div>
  </section>

</body>
</html>
```